Modern Business Card

Modern professional business card with more than just logo and demographic info. Something memorable.

We are a trendy/modern chiropractic group with an emphasis on neurology, hence the minimalist-type brain logo. We want to convey that modern and technical aspect with professionalism and the elite nature of our practice environment.

```html
<!DOCTYPE html>
<html lang="en">
<head>
<meta charset="utf-8">
<title>Vantage Chiropractic – Business Card</title>
<link href="https://fonts.googleapis.com/css2?family=Lora:wght@400&family=Saira+Semi+Condensed:wght@500&display=swap" rel="stylesheet">
<style>
  :root {
    --backdrop: #b7b7b7;
    --brand-blue: #3d62a0;
    --brand-blue-deep: #375a94;
    --paper: #f1f1f1;
    --paper-shade: #e2e2e2;
    --ink: #1c1a1b;
    --light-text: #e9eaee;
    --edge: #3b3035;
  }
  * { margin: 0; padding: 0; box-sizing: border-box; }
  html, body {
    width: 1200px; height: 576px; overflow: hidden;
    background: var(--backdrop);
  }
  .canvas { position: relative; width: 1200px; height: 576px; }

  .card {
    position: absolute;
    border-radius: 11px;
    overflow: hidden;
    box-shadow: 0 3px 6px rgba(0,0,0,0.22);
  }

  /* Front */
  .card--front {
    left: 82px; top: 139px; width: 484px; height: 293px;
    background: linear-gradient(180deg, var(--brand-blue) 0%, var(--brand-blue-deep) 100%);
  }
  .wordmark {
    position: absolute; left: 0; right: 0;
    text-align: center;
    font-family: "Lora", Georgia, serif;
    font-weight: 400;
    color: var(--light-text);
    line-height: 1;
  }
  .wordmark--front-main { top: 102px; font-size: 66px; letter-spacing: 0.5px; }
  .wordmark--front-sub  { top: 168px; font-size: 35px; letter-spacing: 0.3px; }

  /* Back */
  .card--back {
    left: 602px; top: 139px; width: 481px; height: 290px;
    background: linear-gradient(180deg, var(--brand-blue) 0%, var(--brand-blue-deep) 100%);
  }
  .card__panel { position: absolute; inset: 0; }

  .holder { position: absolute; left: 22px; top: 24px; color: var(--light-text); }
  .holder__name {
    font-family: "Saira Semi Condensed", "Arial Narrow", sans-serif;
    font-weight: 500; font-size: 20px; line-height: 1;
  }
  .holder__role {
    margin-top: 6px;
    font-family: "Lora", Georgia, serif; font-size: 12.5px;
  }

  .contacts {
    position: absolute; left: 22px; top: 167px;
    list-style: none;
    font-family: "Lora", Georgia, serif; font-size: 12.5px;
    color: var(--light-text);
  }
  .contacts li { display: flex; align-items: center; height: 18px; }
  .contacts svg { width: 11px; height: 11px; margin-right: 11px; fill: var(--light-text); }
  .address {
    position: absolute; left: 22px; top: 225px;
    font-family: "Lora", Georgia, serif; font-size: 12.5px; line-height: 18px;
    color: var(--light-text);
  }

  .brand-dot {
    position: absolute; left: 331px; top: 72px;
    width: 54px; height: 54px; border-radius: 50%;
    background: var(--brand-blue);
  }
  .wordmark--back-main {
    left: 250px; right: 0; top: 153px;
    font-size: 41px; color: var(--ink);
  }
  .wordmark--back-sub {
    left: 250px; right: 0; top: 195px;
    font-size: 23px; color: var(--ink);
  }
</style>
</head>
<body>
<main class="canvas">

  <section class="card card--front" aria-label="Card front">
    <p class="wordmark wordmark--front-main">VANTAGE</p>
    <p class="wordmark wordmark--front-sub">CHIROPRACTIC</p>
  </section>

  <section class="card card--back" aria-label="Card back">
    <svg class="card__panel" viewBox="0 0 481 290" width="481" height="290" aria-hidden="true">
      <defs>
        <linearGradient id="paperTone" x1="0" y1="0" x2="1" y2="1">
          <stop offset="0" stop-color="var(--paper)"/>
          <stop offset="1" stop-color="var(--paper-shade)"/>
        </linearGradient>
      </defs>
      <path d="M274 0 Q196 145 262 290 L481 290 L481 0 Z" fill="var(--edge)"/>
      <path d="M279 0 Q202 145 268 290 L481 290 L481 0 Z" fill="url(#paperTone)"/>
    </svg>

    <div class="holder">
      <p class="holder__name">Daniel Reed Hale</p>
      <p class="holder__role">Managing Director</p>
    </div>

    <ul class="contacts">
      <li>
        <svg viewBox="0 0 12 12"><path d="M1 3 Q1 1 3 1 L9 1 Q11 1 11 3 L11 4 L8 4 L8 3 L4 3 L4 4 L1 4 Z M3 5 L9 5 L10 11 L2 11 Z"/></svg>
        555-014-2283
      </li>
      <li>
        <svg viewBox="0 0 12 12"><path d="M0 2 H12 V10 H0 Z M1 3 L6 7 L11 3" fill="none" stroke="#e9eaee" stroke-width="1.2"/></svg>
        dan@vantagechiropractic.com
      </li>
      <li>
        <svg viewBox="0 0 12 12"><circle cx="6" cy="6" r="5" fill="none" stroke="#e9eaee" stroke-width="1.1"/><path d="M1 6 H11 M6 1 Q3 6 6 11 Q9 6 6 1" fill="none" stroke="#e9eaee" stroke-width="1"/></svg>
        www.vantagechiropractic.com
      </li>
    </ul>

    <p class="address">418 Meridian Ave., Fairview,<br>Lakeside, US 204518</p>

    <div class="brand-dot" aria-hidden="true"></div>
    <p class="wordmark wordmark--back-main">VANTAGE</p>
    <p class="wordmark wordmark--back-sub">CHIROPRACTIC</p>
  </section>

</main>
</body>
</html>
```